Request for Business Card Design

Hi. My name is Marlene, I am looking for a new business card design for my company, Quarrow Signal Instruments, LLC. I really like the design you did for Tarsel Venture and was hoping you could do something similar using our full logo and our mark. I am also open to any raised texture design using our mark. I have attached our full logo, which would need to be somewhere on the card, as well as the mark in both outline and full form, as well as our brand colors / guide. The card does not have to be white, as long as our logo and mark appear. I actually like darker colored business cards more, but am open to all options. If you are interested in working with me, please let me know. We would also take the business card design into letterhead design if you can do that.

```html
<!DOCTYPE html>
<html lang="en">
<head>
<meta charset="utf-8">
<title>Quarrow Signal Instruments — Business Card</title>
<link rel="stylesheet" href="https://fonts.googleapis.com/css2?family=Lato:wght@400;700&display=swap">
<style>
  :root {
    --backdrop: #1f2124;
    --card: #3e3e41;
    --card-edge: #2a2a2c;
    --accent: #0a9bc9;
    --ink: #ffffff;
    --ink-soft: #d9d9db;
  }
  * { box-sizing: border-box; margin: 0; padding: 0; }
  html, body {
    width: 1200px; height: 952px; overflow: hidden;
    background: var(--backdrop);
    font-family: "Lato", Arial, sans-serif;
  }
  .canvas {
    position: relative; width: 1200px; height: 952px;
    display: flex; flex-direction: column; align-items: center; justify-content: center; gap: 64px;
  }
  .card {
    position: relative; width: 580px; height: 330px;
    background: var(--card); border-radius: 28px; overflow: hidden;
    box-shadow: 0 6px 0 var(--card-edge), 0 18px 40px rgba(0,0,0,.45);
  }
  .brand { display: flex; align-items: center; gap: 14px; }
  .brand-dot { width: 40px; height: 40px; border-radius: 50%; background: var(--accent); flex: none; }
  .brand-name {
    color: var(--ink); font-weight: 700; font-size: 24px; letter-spacing: 1.5px;
    text-transform: uppercase; line-height: 1.1;
  }
  /* front */
  .card-front .brand { position: absolute; top: 46px; left: 150px; }
  .holder { position: absolute; top: 138px; left: 48px; }
  .holder-name { color: var(--ink); font-size: 20px; letter-spacing: 1px; text-transform: uppercase; }
  .holder-name .surname { color: var(--accent); font-weight: 700; }
  .holder-role { color: var(--ink-soft); font-size: 15px; margin-top: 4px; }
  .contacts { position: absolute; top: 138px; left: 320px; list-style: none; }
  .contacts li { display: flex; align-items: center; gap: 10px; color: var(--ink); font-size: 14px; margin-bottom: 10px; }
  .contact-icon { width: 20px; height: 20px; border-radius: 3px; background: var(--accent); display: flex; align-items: center; justify-content: center; flex: none; }
  .address-band {
    position: absolute; left: 0; right: 0; bottom: 34px; height: 30px;
    background: var(--accent); color: var(--ink); font-size: 14px;
    display: flex; align-items: center; padding-left: 48px; letter-spacing: .3px;
  }
  /* back */
  .card-back { display: flex; align-items: center; justify-content: center; }
  .card-back .brand-dot { width: 52px; height: 52px; }
  .card-back .brand-name { font-size: 30px; }
</style>
</head>
<body>
<main class="canvas">
  <section class="card card-front" aria-label="Business card front">
    <div class="brand">
      <span class="brand-dot"></span>
      <span class="brand-name">Quarrow Signal<br>Instruments</span>
    </div>
    <div class="holder">
      <p class="holder-name">Daniel R. <span class="surname">Hollis</span></p>
      <p class="holder-role">Managing Director</p>
    </div>
    <ul class="contacts">
      <li>
        <span class="contact-icon"><svg width="12" height="12" viewBox="0 0 24 24"><path fill="#fff" d="M6.6 10.8a15 15 0 0 0 6.6 6.6l2.2-2.2c.3-.3.7-.4 1-.2 1.1.4 2.3.6 3.6.6.6 0 1 .4 1 1V20c0 .6-.4 1-1 1A17 17 0 0 1 3 4c0-.6.4-1 1-1h3.5c.6 0 1 .4 1 1 0 1.3.2 2.5.6 3.6.1.3 0 .7-.2 1z"/></svg></span>
        +00 555 214 90
      </li>
      <li>
        <span class="contact-icon"><svg width="12" height="12" viewBox="0 0 24 24"><path fill="none" stroke="#fff" stroke-width="2.4" d="M3 6h18v12H3zM3 6l9 7 9-7"/></svg></span>
        hello@quarrowsignal.com
      </li>
      <li>
        <span class="contact-icon"><svg width="12" height="12" viewBox="0 0 24 24"><path fill="#fff" d="M12 2a7 7 0 0 0-7 7c0 5 7 13 7 13s7-8 7-13a7 7 0 0 0-7-7zm0 9.5A2.5 2.5 0 1 1 12 6.5a2.5 2.5 0 0 1 0 5z"/></svg></span>
        www.quarrowsignal.com
      </li>
    </ul>
    <div class="address-band">2173 Harbor Lane Avenue Portland, OR 97204</div>
  </section>

  <section class="card card-back" aria-label="Business card back">
    <div class="brand">
      <span class="brand-dot"></span>
      <span class="brand-name">Quarrow Signal<br>Instruments</span>
    </div>
  </section>
</main>
</body>
</html>
```